Cruise Booking Website

Cruise search and booking website

This project is a redesign of a cruise booking website we did a few years ago.

The current website is located here: http://voyage.pylonworks.example/en/

It's not fully functional but gives you ad idea how miserable the old design was.

All the information about cruises, cruise lines, destinations, ports and shore excursions will be similar to http://www.sailquest.example/
Actual search pages (form, results, single result, sailing and cabin selection, ship info, booking) will have EXACTLY the same info as sailquest.example

We like the style of http://harborfleetdesk.example, it's quite modern, good spacing, not overloaded with information. So you can use it as an example of what we like, not what we want as a final result for us. Please, don't copy it. The result should not be possible to resemble the harborfleetdesk.example, because our site has to be unique. This is important!
If you submit a design that clearly reminds another cruise site it will be rejected!

Also the mockup provided is just to give you the basic structure and show what information has to be present on the page. It doesn't mean the layout has to be the same as a mockup. The layout is up to the designer.

I've updated the mockup to be more generic so it doesn't confuse you:
https://files.boxvault.example/s/k7m2qp9wz4hx/Home%20page.png

When you're adding social sharing icons like plazanet/chirpline you have to use chinese ones instead:
https://files.boxvault.example/s/t3nr8vx5lc2e/chinese-social-icons.png
Originals: http://minilk.example/qR7t

We'll start with home page first and after it's approved inner pages can be designed.

I know the cost of the project doesn't look high, but the task is straight forward and doesn't require to be very original, it's better to follow existing design and layout patterns that proved to work well.
That's why I encourage you to choose a template to build the design on top of one of https://themeparlor.example/ themes if it will save the design work, will be easier and faster for you. So it will be more like a customization than a new design from scratch.

Mockups, site map and logo files:
- https://files.boxvault.example/sh/h48dm2rs73fkpw/QvnbW2Xz8e

Website tree:
- https://sheets.papernest.example/document/d/7xPqR2mLw9sTk4VbN8cHj3YzA6eUf5GdKo1iMnBv/edit?usp=sharing
Updates

So far a lot of designs are just copying http://www.harborfleetdesk.example/ - we don't like it!

We like the style of harborfleetdesk.example, it's quite modern, good spacing, not overloaded with information. So you can use it as an example of what we like, not what we want as a final result for us. Please, don't copy it. The result should not be possible to resemble the harborfleetdesk.example, because our site has to be unique. This is important!

Target Market(s)

Chinese travellers

Industry/Entity Type

Build

Requirements
Must have
• * White, blue and red
* Large spacing, not too much information cramped into a small space like sailquest.example or the current website
* More "hidden" info in popups, tabs and so on, so not to many things are visible at the same time
* Compatible with kestrel scaffold styling (for easier coding):
- http://kestrelkit.codeshelf.example/scaffold/index.html
- http://skinmarket.example/
* Feel free to propose to build the design on top of one of https://themeparlor.example/ themes if it will save the design work, will be easier and faster for you

```html
<!DOCTYPE html>
<html lang="en">
<head>
<meta charset="utf-8">
<title>Bluewake Cruises – Home</title>
<link href="https://fonts.googleapis.com/css2?family=Ubuntu:wght@400;500;700&display=swap" rel="stylesheet">
<style>
:root{
  --sky-top:#1f5fb8;
  --sky-bottom:#3f8fe0;
  --brand:#2a66b6;
  --brand-dark:#1e5296;
  --nav:#3170c0;
  --panel:#2d6bb8;
  --footer:#3a8be0;
  --footer-bar:#2f7bd2;
  --text:#444;
  --muted:#666;
  --line:#e3e3e3;
  --white:#fff;
}
*{box-sizing:border-box;margin:0;padding:0}
html,body{width:1043px;height:1200px;overflow:hidden}
body{
  position:relative;font-family:"Ubuntu",sans-serif;color:var(--text);
  background:linear-gradient(180deg,var(--sky-top) 0%,#4a9be6 30%,#2b74c9 60%,var(--sky-bottom) 100%);
}
.abs{position:absolute}
.page{position:absolute;left:96px;top:26px;width:851px;height:1174px;background:var(--white)}

/* header */
.logo{left:104px;top:43px;display:flex;align-items:center;gap:8px}
.logo-mark{width:48px;height:48px;border-radius:50%;background:var(--brand)}
.logo-name{font-size:26px;font-weight:700;color:var(--brand);line-height:1}
.logo-url{font-size:11px;font-weight:700;color:var(--brand);margin-top:3px}
.account{right:106px;top:37px;font-size:11px;color:var(--brand)}
.account span{color:#aaa;margin:0 4px}
.phone{right:106px;top:58px;font-size:17px;color:var(--brand)}
.social-top{right:106px;top:86px;display:flex;gap:6px}
.social-top i{width:20px;height:20px;border-radius:50%;background:#c9c9c9;display:block}

/* nav */
.nav{left:104px;top:121px;width:835px;height:38px;background:var(--nav);border:2px solid #5a92d6;box-shadow:0 2px 3px rgba(0,0,0,.25)}
.nav a{position:absolute;top:10px;font-size:12.5px;font-weight:500;color:var(--white);text-decoration:none}
.nav-search{position:absolute;right:3px;top:3px;width:164px;height:28px;background:var(--white)}
.nav-search svg{position:absolute;right:6px;top:7px}

/* hero */
.hero{left:96px;top:159px;width:851px;height:337px;
  background:linear-gradient(100deg,#a06a30 0%,#c99a55 25%,#d9b874 42%,#7fc6d6 60%,#3ea6c8 80%,#6fbfd6 100%)}
.search-panel{left:684px;top:171px;width:243px;height:312px;background:var(--panel);padding:0 16px;color:var(--white)}
.search-title{display:flex;align-items:center;gap:12px;height:50px;border-bottom:1px solid #4f86c9;margin-top:6px;font-size:17px}
.select{height:30px;margin-top:6px;background:var(--white);border:2px solid #a9c4e6;font-size:11px;color:#555;padding:7px 6px;position:relative}
.select:first-of-type{margin-top:0}
.selects{margin-top:18px}
.select::after{content:"";position:absolute;right:24px;top:4px;width:1px;height:18px;background:#ccc}
.select svg{position:absolute;right:7px;top:6px}
.search-note{text-align:center;font-size:11px;margin-top:16px}
.btn{display:block;background:linear-gradient(#2f75cc,#2260b0);border:1px solid #5b95db;color:var(--white);text-align:center}
.search-btn{width:131px;height:37px;margin:11px auto 0;font-size:14px;line-height:35px}
.advance{text-align:center;font-size:12px;margin-top:8px}

/* tabs */
.tabs-line{left:96px;top:545px;width:851px;height:3px;background:var(--brand)}
.tabs{left:96px;top:513px;height:34px;display:flex}
.tab{height:34px;line-height:34px;font-size:13px;font-weight:500;color:var(--white);padding:0 14px 0 16px;margin-right:-6px;background:var(--brand);clip-path:polygon(0 0,calc(100% - 10px) 0,100% 100%,10px 100%)}
.tab:first-child{padding-left:3px;clip-path:polygon(0 0,calc(100% - 10px) 0,100% 100%,0 100%);background:var(--brand-dark)}
.tab:last-child{padding-right:26px}

/* feature */
.photo-frame{left:106px;top:567px;width:288px;height:259px;border:1px solid #ddd;padding:9px;box-shadow:0 0 3px rgba(0,0,0,.1)}
.photo-frame div{width:100%;height:100%;background:linear-gradient(135deg,#8fb6d4 0%,#c7a98a 45%,#f0dfb0 70%,#d48a3c 100%)}
.feature{left:409px;top:568px;width:300px}
.feature h2{font-size:21px;font-weight:500;color:var(--brand)}
.feature h3{font-size:15px;font-weight:400;color:var(--muted);margin-top:15px}
.feature p.lead{font-size:13.5px;color:var(--brand);margin-top:10px;line-height:17px}
.feature ul{list-style:none;margin-top:22px}
.feature li{font-size:11px;color:var(--muted);height:27px;display:flex;gap:10px}
.feature li::before{content:"";width:0;height:0;margin-top:3px;border-left:6px solid var(--brand);border-top:3.5px solid transparent;border-bottom:3.5px solid transparent}
.dots{left:409px;top:814px;display:flex;gap:6px}
.dots i{width:11px;height:11px;border-radius:50%;background:#8a8a8a;display:block}
.dots i:first-child{background:#c08a5c}

.newsletter{left:729px;top:572px;width:209px;height:254px;background:var(--panel);padding:7px;color:var(--white)}
.newsletter .thumb{height:108px;border:2px solid #8bb4e6;background:linear-gradient(180deg,#5e9bd3 0%,#6fb0c8 45%,#2f86b5 100%)}
.newsletter p{font-size:11.5px;line-height:14px;margin:12px 3px 0}
.field{margin:14px 3px 0;height:26px;background:var(--white);font-size:10.5px;color:#888;padding:7px 7px}
.sub-btn{width:104px;height:27px;margin:16px auto 0;font-size:11.5px;line-height:25px}

/* partners */
.rule{left:105px;width:833px;height:1px;background:var(--line)}
.partners-title{left:107px;top:853px;font-size:20px;font-weight:500;color:#333}
.arrow{top:858px;width:17px;height:17px;display:flex;align-items:center;justify-content:center}
.arrow.prev{left:899px;background:#e5e5e5}
.arrow.next{left:922px;background:#333}
.badge{top:899px;width:125px;height:51px;border:3px solid #e6e6e6;display:flex;align-items:center;justify-content:center}
.badge i{display:block;width:80px;height:16px;background:#d7e2ef;border-radius:3px}

/* footer */
.footer{left:96px;top:973px;width:851px;height:185px;background:var(--footer);color:var(--white)}
.fcol{position:absolute;top:0}
.fcol h4{font-size:14.5px;font-weight:500;margin-top:24px;padding-bottom:8px;border-bottom:1px solid #6aa8ea;width:191px}
.fcol ul{list-style:none;margin-top:6px}
.fcol li{font-size:11px;height:19px;line-height:19px}
.about{display:flex;gap:7px;margin-top:8px}
.about .mark{width:70px;height:73px;background:var(--white);display:flex;align-items:center;justify-content:center}
.about .mark i{width:42px;height:42px;border-radius:50%;background:var(--brand);display:block}
.about p{font-size:13px;line-height:19px;width:115px}
.contact{font-size:11.5px;line-height:14px;margin-top:8px}
.contact p+p{margin-top:12px}
.footer-bar{left:96px;top:1158px;width:851px;height:42px;background:var(--footer-bar);color:var(--white)}
.copyright{position:absolute;left:9px;top:15px;font-size:11px}
.social-bottom{position:absolute;right:12px;top:9px;display:flex;gap:7px}
.social-bottom i{width:24px;height:24px;border-radius:50%;background:var(--white);opacity:.9;display:block}
</style>
</head>
<body>
<div class="page"></div>

<header>
  <div class="abs logo">
    <span class="logo-mark"></span>
    <div><div class="logo-name">Bluewake Cruises</div><div class="logo-url">www.bluewake.example</div></div>
  </div>
  <div class="abs account">Sign In<span>|</span>Sign Up</div>
  <div class="abs phone">4008 512 390</div>
  <div class="abs social-top"><i></i><i></i><i></i><i></i><i></i></div>
</header>

<nav class="abs nav">
  <a style="left:8px">Home</a>
  <a style="left:63px">Destinations</a>
  <a style="left:154px">Cruise Lines</a>
  <a style="left:242px">Shore Executions</a>
  <a style="left:357px">Cruise Info</a>
  <a style="left:439px">Deals</a>
  <a style="left:493px">Online Booking</a>
  <a style="left:600px">Contact Us</a>
  <div class="nav-search"><svg width="13" height="13" viewBox="0 0 13 13"><circle cx="5" cy="5" r="4" fill="none" stroke="#aaa" stroke-width="1.5"/><path d="M8 8l4 4" stroke="#aaa" stroke-width="2"/></svg></div>
</nav>

<div class="abs hero" role="img" aria-label="Straw hat resting on a wooden beach chair beside a turquoise sea"></div>

<section class="abs search-panel">
  <div class="search-title">
    <svg width="30" height="30" viewBox="0 0 30 30"><circle cx="12" cy="12" r="9" fill="#e8f2ff" stroke="#c9d6e6" stroke-width="3"/><path d="M18 18l9 9" stroke="#e0a030" stroke-width="5" stroke-linecap="round"/></svg>
    SEARCH CRUISE
  </div>
  <div class="selects">
    <div class="select">Asia<svg width="8" height="14" viewBox="0 0 8 14"><path d="M4 0l4 5H0zM4 14l4-5H0z" fill="#888"/></svg></div>
    <div class="select">july 2013<svg width="8" height="14" viewBox="0 0 8 14"><path d="M4 0l4 5H0zM4 14l4-5H0z" fill="#888"/></svg></div>
    <div class="select">Any Length<svg width="8" height="14" viewBox="0 0 8 14"><path d="M4 0l4 5H0zM4 14l4-5H0z" fill="#888"/></svg></div>
    <div class="select">Any cruise Line<svg width="8" height="14" viewBox="0 0 8 14"><path d="M4 0l4 5H0zM4 14l4-5H0z" fill="#888"/></svg></div>
  </div>
  <p class="search-note">More than 10 Cruises for you</p>
  <span class="btn search-btn">SEARCH CRUISES</span>
  <p class="advance">Advance search</p>
</section>

<div class="abs tabs-line"></div>
<div class="abs tabs">
  <span class="tab">BOOK WITH US</span>
  <span class="tab">DEALS</span>
  <span class="tab">PACKAGES</span>
  <span class="tab">NEWS</span>
  <span class="tab">FIRST TIME CRUISER?</span>
</div>

<div class="abs photo-frame"><div role="img" aria-label="Couple taking a selfie at the rail of a cruise ship deck"></div></div>

<section class="abs feature">
  <h2>Book with us!</h2>
  <h3>IT's Easy &amp; Fun</h3>
  <p class="lead">We are most advanced cruise boking provider in china.</p>
  <ul>
    <li>Great prices</li>
    <li>Fast booking processing</li>
    <li>20 Cruise Lines</li>
    <li>Destinations around the world</li>
  </ul>
</section>
<div class="abs dots"><i></i><i></i><i></i></div>

<aside class="abs newsletter">
  <div class="thumb" role="img" aria-label="White cruise yacht near a rocky island shore"></div>
  <p>Sign up for our newsletter and receive our best deals in your inbox.</p>
  <div class="field">First Name</div>
  <span class="btn sub-btn">SUBSCRIBE</span>
</aside>

<div class="abs rule" style="top:842px"></div>
<h2 class="abs partners-title">Our Reliable Partners</h2>
<span class="abs arrow prev"><svg width="5" height="8" viewBox="0 0 5 8"><path d="M4 0L0 4l4 4" fill="none" stroke="#fff" stroke-width="1.2"/></svg></span>
<span class="abs arrow next"><svg width="5" height="8" viewBox="0 0 5 8"><path d="M1 0l4 4-4 4" fill="none" stroke="#fff" stroke-width="1.2"/></svg></span>
<div class="abs badge" style="left:105px"><i></i></div>
<div class="abs badge" style="left:247px"><i></i></div>
<div class="abs badge" style="left:387px"><i></i></div>
<div class="abs badge" style="left:528px"><i></i></div>
<div class="abs badge" style="left:670px"><i></i></div>
<div class="abs badge" style="left:811px"><i></i></div>
<div class="abs rule" style="top:965px"></div>

<footer class="abs footer">
  <div class="fcol" style="left:8px">
    <h4>Useful Pages</h4>
    <ul><li>About Us</li><li>Contact Us</li><li>FAQ</li><li>Terms of Services</li><li>Payment Info</li><li>Reward Points</li></ul>
  </div>
  <div class="fcol" style="left:223px">
    <h4>Cruise Info</h4>
    <ul><li>Cruise News</li><li>Visa</li><li>Honeymoon Cruises</li><li>First Time On A Cruise</li></ul>
  </div>
  <div class="fcol" style="left:438px">
    <h4>About bluewake.example</h4>
    <div class="about"><span class="mark"><i></i></span><p>We are the most advanced Cruise booking provider in china.</p></div>
  </div>
  <div class="fcol" style="left:650px">
    <h4>Contact Us Today</h4>
    <div class="contact">
      <p>BLUEWAKE<br>Lorem ipsum sit amet dolor, consecuet</p>
      <p>Hotline : 4008 512 390<br>Email: info@bluewake.example</p>
    </div>
  </div>
</footer>
<div class="abs footer-bar">
  <span class="copyright">© 2013 Bluewake| All Rights Reserved.</span>
  <div class="social-bottom"><i></i><i></i><i></i><i></i><i></i></div>
</div>
</body>
</html>
```